VENTURE CAPITAL GROUP BUSINESS CARD DESIGN

Venture Capital Group based in SF looking for a bold business card design. No trendy colour explosion, 3D effects etc. Just "simple" optical effects. Works on your brain, keeps your eye focused and sticks to your mind.
Target Market(s)
Technology startups
Industry/Entity Type
Venture Capital
Contact Information for Business Card
DESMOND WHITLAKE
MANAGING PARTNER
187 FENWORTH ST SAN FRANCISCO, CA 94187
415.555.0142 O
415.555.0147 F
415.555.0193 C
desmond@veldtmoorcapital.ventures

```html
<!DOCTYPE html>
<html lang="en">
<head>
<meta charset="utf-8">
<title>Veldtmoor Capital Group — Business Card</title>
<link rel="stylesheet" href="https://fonts.googleapis.com/css2?family=Open+Sans:wght@300;400;600&display=swap">
<style>
  :root {
    --bg: #e9e7e3;
    --paper: #ffffff;
    --green: #2f8f3a;
    --green-dark: #1f6e2a;
    --ink: #3a3a3a;
    --muted: #8a8a8a;
    --rule: #c9c9c9;
    --back-light: #a9a9ab;
    --back-dark: #5e5e61;
  }
  * { box-sizing: border-box; margin: 0; padding: 0; }
  html, body { width: 1200px; height: 950px; overflow: hidden; }
  body {
    background: var(--bg);
    font-family: "Open Sans", Arial, sans-serif;
    position: relative;
  }
  .card {
    position: absolute;
    left: 250px;
    width: 700px;
    height: 400px;
    border-radius: 22px;
    box-shadow: 0 10px 28px rgba(0,0,0,.18);
    overflow: hidden;
  }
  /* Front */
  .card-front { top: 50px; background: var(--paper); border-bottom: 8px solid var(--green); }
  .brand {
    position: absolute; top: 62px; right: 190px;
    display: flex; align-items: center; gap: 16px;
  }
  .brand-dot { width: 46px; height: 46px; border-radius: 50%; background: var(--green); }
  .brand-name {
    font-weight: 400; font-size: 28px; letter-spacing: 3px;
    color: var(--green); line-height: 1.1;
  }
  .divider-v {
    position: absolute; top: 40px; bottom: 40px; right: 160px;
    width: 1px; background: var(--rule);
  }
  .address {
    position: absolute; top: 60px; right: 30px; width: 115px;
    font-size: 16px; line-height: 1.45; color: var(--ink); text-align: right; font-weight: 300;
  }
  .person { position: absolute; left: 44px; bottom: 150px; }
  .person-name { font-size: 30px; font-weight: 600; color: var(--green); }
  .person-title { font-size: 17px; color: var(--muted); font-weight: 400; margin-top: 2px; }
  .divider-h {
    position: absolute; left: 44px; right: 200px; bottom: 140px;
    height: 1px; background: var(--rule);
  }
  .contacts {
    position: absolute; left: 44px; bottom: 24px;
    list-style: none; font-size: 16px; color: var(--ink); line-height: 1.55; font-weight: 300;
  }
  .contacts li { display: flex; align-items: center; gap: 12px; }
  .contacts svg { width: 16px; height: 16px; fill: var(--ink); flex: none; }

  /* Back */
  .card-back {
    top: 500px;
    background: radial-gradient(ellipse at 60% 45%, var(--back-light), var(--back-dark) 85%);
  }
  .back-brand {
    position: absolute; top: 50%; left: 50%; transform: translate(-50%, -50%);
    display: flex; align-items: center; gap: 18px;
  }
  .back-brand .brand-dot { width: 90px; height: 90px; background: #f2f2f2; }
  .back-brand .brand-name { color: #ffffff; font-size: 30px; }
  .web {
    position: absolute; left: 44px; top: 200px;
    transform: translate(-50%, -50%) rotate(-90deg);
    transform-origin: center;
    white-space: nowrap; font-size: 17px; letter-spacing: 1px;
    color: #f0f0f0; font-weight: 300;
  }
</style>
</head>
<body>
  <section class="card card-front" aria-label="Card front">
    <div class="brand">
      <span class="brand-dot"></span>
      <span class="brand-name">VELDTMOOR<br>CAPITAL GROUP</span>
    </div>
    <div class="divider-v"></div>
    <p class="address">187 Fenworth ST<br>San Francisco<br>CA 94187</p>

    <div class="person">
      <h1 class="person-name">Desmond Whitlake</h1>
      <p class="person-title">Managing Partner</p>
    </div>
    <div class="divider-h"></div>

    <ul class="contacts">
      <li>
        <svg viewBox="0 0 16 16"><path d="M3 1l3 3-1.5 2a9 9 0 0 0 5.5 5.5L12 10l3 3-2 2C7 15 1 9 1 3z"/></svg>
        415.555.0142
      </li>
      <li>
        <svg viewBox="0 0 16 16"><path d="M4 1h8v14H4zM5.5 2.5v9h5v-9z"/></svg>
        415.555.0193
      </li>
      <li>
        <svg viewBox="0 0 16 16"><path d="M4 1h7v4H4zM2 6h12v8H2zM4 9h8v1H4z"/></svg>
        415.555.0147
      </li>
      <li>
        <svg viewBox="0 0 16 16"><path d="M1 3h14v10H1zM2.5 4.5L8 9l5.5-4.5v-.2L8 8 2.5 4.3z"/></svg>
        desmond@veldtmoorcapital.ventures
      </li>
    </ul>
  </section>

  <section class="card card-back" aria-label="Card back">
    <p class="web">www.veldtmoorcapital.ventures</p>
    <div class="back-brand">
      <span class="brand-dot"></span>
      <span class="brand-name">VELDTMOOR</span>
    </div>
  </section>
</body>
</html>
```